Hop Along Days campaign: promoting kids play in the UK - Website Redesign

Hop Along Days is a national UK campaign that promotes the value of play for children. The current website is live at http://www.hopalongdays.co.uk. This website has been live for 4 years and now needs to be redesigned. The target audience is parents of young children up to the age of 12.

The current site was designed with a series of old adverts in mind. Here is an example of an old advert: http://vidshare.example/qR7tLm2XwZa

Criticisms of existing site:
The design represented the adverts too closely. The result was a website that mirrors the adverts rather than complements them.
The color scheme is too dark.
Text-heavy pages (e.g. http://www.hopalongdays.co.uk/fun.php) are dull and not FUN!

New site
We have recently had a series of new video adverts produced:
advert 1: http://vidshare.example/hB4nVc8JsPe
advert 2: http://vidshare.example/KgW3rTy9DuM
advert 3: http://vidshare.example/zA5oEi1HbNq

The new site should be cleaner and brighter than the existing site, possibly with a white background using graphics, fonts and advert characters (see attached character graphics files) to add the element of fun and play.

The homepage should include:
1. Hop Along Days logo (attached)
2. Social Media links (visible on all pages of the site) – Chatterbook, Chirpline, ClipVault
3. Link to the HopAlongDays app page of the site (visible on all pages)
4. Image/video placeholder that the user can scroll through, view full-size images and play videos.
5. Text area to hold approximately 100 words describing the purpose of the campaign
6. Site footer to contain the same information as on the existing site along with the Northern Games & Crafts Guild logo (attached)

Site structure:
One change to the site structure… the “Brought to you by” menu item will be removed from the top-level menu.

General:
Some pages on the existing site are quite text-heavy, we would like to break up text on these pages in some way. Graphical division of paragraphs, use of advert characters?

Please note that all attached graphics file are the property of the Northern Games & Crafts Guild and must only be used for the purpose of this project.

```html
<!DOCTYPE html>
<html lang="en">
<head>
<meta charset="utf-8">
<title>Hop Along Days</title>
<link href="https://fonts.googleapis.com/css2?family=Lato:wght@400;700;900&display=swap" rel="stylesheet">
<style>
:root{
  --blue:#0c8fd6;
  --pink:#e63a5f;
  --green:#8cb81a;
  --purple:#322a6e;
  --yellow:#fde23a;
  --ink:#3a3a3a;
  --navy:#2c3358;
  --sky:#e8f4fb;
  --paper:#ffffff;
}
*{box-sizing:border-box;margin:0;padding:0}
html,body{width:925px;height:1200px;overflow:hidden}
body{position:relative;font-family:'Lato',sans-serif;color:var(--ink);
  background:linear-gradient(180deg,#eef7fc 0%,#f6f9fb 40%,#f3f6f8 100%)}
.abs{position:absolute}
.art{position:absolute;border-radius:10px}

/* header */
.logo-cloud{left:374px;top:4px;width:176px;height:92px;background:#fff;border-radius:60px 60px 40px 40px;
  display:flex;align-items:center;justify-content:center}
.logo-name{font-weight:900;font-size:20px;color:var(--pink);font-family:'Lato',sans-serif}
.phone{left:628px;top:10px;display:flex;align-items:center;gap:6px;font-size:18px;color:#333}
.social{right:117px;top:46px;display:flex;gap:8px;font-size:9px;font-weight:700}
.social a{text-decoration:none}
.social .s1{color:#3b5a9a}.social .s2{color:var(--blue)}.social .s3{color:#d22}

/* nav */
.nav{left:110px;top:98px;width:705px;height:46px;background:#fff;border-radius:3px;
  box-shadow:0 1px 2px rgba(0,0,0,.05)}
.nav a{position:absolute;top:15px;font-size:11.5px;font-weight:700;text-decoration:none;transform:translateX(-50%);white-space:nowrap}
.nav .home{background:var(--yellow);color:var(--navy);padding:5px 14px;top:9px;border-radius:3px;transform:translateX(-50%) rotate(-1deg)}

/* main panel */
.panel{left:110px;top:200px;width:708px;height:856px;background:var(--paper);border-radius:14px 14px 0 0}
.download{left:640px;top:158px;width:166px;height:42px;background:var(--yellow);transform:rotate(-1deg);
  display:flex;align-items:center;gap:8px;padding-left:14px;font-size:12px;font-weight:700;line-height:1.35}
.download .app{width:16px;height:26px;border:2px solid var(--navy);border-radius:3px;background:#bfe37a}
.download .a1{color:var(--pink)}.download .a2{color:var(--navy)}

.slider{left:124px;top:210px;width:464px;height:266px;background:var(--green);border-radius:14px;transform:rotate(-.6deg)}
.slide{left:148px;top:224px;width:432px;height:240px;border-radius:12px;
  background:linear-gradient(135deg,#c9c2b0 0%,#e8e2d6 45%,#d46a4a 75%,#4a8fd0 100%)}
.dots{left:164px;top:446px;display:flex;gap:8px}
.dots span{width:11px;height:11px;border-radius:50%;background:#fff}
.dots span:first-child{background:var(--purple)}

.video-box{left:606px;top:256px;width:196px;height:230px;background:#fff;border-radius:12px;
  box-shadow:0 2px 6px rgba(0,0,0,.15)}
.video-title{left:606px;top:276px;width:196px;text-align:center;color:var(--pink);font-size:19px;font-weight:700}
.rule{height:2px;background:#c5c8d6;border-radius:2px}
.video-thumb{left:614px;top:314px;width:180px;height:106px;border:5px solid #3c3f86;border-radius:10px;
  background:linear-gradient(135deg,#c79b5a,#a7773d)}
.play{left:690px;top:360px;width:26px;height:26px;border-radius:50%;background:#fff;display:flex;align-items:center;justify-content:center}
.vbtn{position:absolute;height:20px;width:82px;font-size:11.5px;font-weight:700;color:var(--navy);
  display:flex;align-items:center;justify-content:center}

/* about */
.about-title{left:0;top:512px;width:925px;text-align:center;font-size:20px;font-weight:700;color:var(--pink)}
.about-text{left:118px;top:554px;width:690px;text-align:center;font-size:10.5px;line-height:18.5px;color:#444}
.more{left:0;top:619px;width:925px;text-align:center;font-size:9.5px;font-weight:700;color:var(--blue)}

/* cards */
.card{position:absolute;top:650px;width:159px;height:204px;color:#fff;text-align:center;
  clip-path:polygon(0 0,100% 0,100% 94%,92% 97%,80% 95%,66% 98%,50% 95%,36% 98%,22% 95%,10% 98%,0 95%)}
.card .arc{position:absolute;left:35px;top:20px;width:88px;height:88px;border:1px solid rgba(255,255,255,.55);border-radius:50%;
  clip-path:inset(0 0 30% 0)}
.card .icon{position:absolute;left:0;top:36px;width:100%;display:flex;justify-content:center}
.card h3{position:absolute;top:93px;width:100%;font-size:15.5px;font-weight:700}
.card p{position:absolute;top:122px;left:14px;right:14px;font-size:9.6px;line-height:14px;opacity:.9}
.card .plus{position:absolute;left:73px;top:172px;width:13px;height:13px;border:1px solid #fff;border-radius:50%;
  font-size:10px;line-height:11px}
.c-blue{left:116px;background:var(--blue)}
.c-pink{left:294px;background:var(--pink)}
.c-green{left:472px;background:var(--green)}
.c-purple{left:650px;background:var(--purple)}

/* gallery */
.gallery-title{left:0;top:882px;width:925px;text-align:center;font-size:20px;font-weight:700}
.gallery-title .a{color:var(--pink)}.gallery-title .b{color:var(--blue)}
.thumb{position:absolute;top:938px;width:151px;height:88px;border:6px solid #f8c11a;border-radius:8px}
.thumb .play{position:absolute;left:50%;top:50%;margin:-13px 0 0 -13px}
.arrow{position:absolute;top:974px;width:13px;height:13px;border:1px solid #7a7fa6;border-radius:50%;
  font-size:8px;color:#7a7fa6;text-align:center;line-height:11px}

/* footer */
.footer{left:0;top:1056px;width:925px;height:144px;background:var(--sky);border-top:1px solid #d5e8f3}
.guild{left:700px;top:1062px;width:108px;text-align:right;font-size:11px;font-weight:700;color:var(--navy);line-height:1.3}
.legal{right:117px;top:1124px;text-align:right;font-size:10px;line-height:14px;color:#333}
</style>
</head>
<body>

<!-- header -->
<div class="art" style="left:128px;top:0;width:144px;height:96px;background:linear-gradient(180deg,#f4c9a0,#e04a4a)" role="img" aria-label="Illustrated girl character holding a stick"></div>
<div class="abs logo-cloud"><span class="logo-name">Hop Along Days</span></div>

<div class="abs phone">
  <svg width="26" height="22" viewBox="0 0 26 22"><path d="M3 8c0-4 4-6 10-6s10 2 10 6l-4 2-2-3H9L7 10z" fill="none" stroke="#555" stroke-width="1.6"/><rect x="5" y="10" width="16" height="10" rx="2" fill="none" stroke="#555" stroke-width="1.6"/><circle cx="13" cy="15" r="2.5" fill="none" stroke="#555" stroke-width="1.4"/></svg>
  <span>+44 (0) 20 7946 0321</span>
</div>
<div class="abs social">
  <a class="s1" href="#">Chatterbook</a><a class="s2" href="#">Chirpline</a><a class="s3" href="#">ClipVault</a>
</div>

<!-- main panel -->
<div class="abs panel"></div>

<nav class="abs nav">
  <a class="home" style="left:46px" href="#">HOME</a>
  <a style="left:157px;color:var(--pink)" href="#">PLAY RIGHT NOW</a>
  <a style="left:292px;color:var(--navy)" href="#">GET INVOLVED</a>
  <a style="left:408px;color:var(--green)" href="#">WHY PLAY</a>
  <a style="left:524px;color:var(--blue)" href="#">FUN FOREVER</a>
  <a style="left:640px;color:var(--navy)" href="#">RESOURCES</a>
</nav>

<div class="abs download"><span class="app"></span><span><span class="a1">HopAlongDays</span><br><span class="a2">DOWNLOAD</span></span></div>

<div class="abs slider"></div>
<div class="abs slide art" role="img" aria-label="Photo of a toddler drawing on paper surrounded by toys"></div>
<div class="abs dots"><span></span><span></span><span></span></div>

<div class="art" style="left:656px;top:200px;width:144px;height:56px;background:linear-gradient(90deg,#8cb8d8,#f2a0b0);border-radius:20px 20px 0 0" role="img" aria-label="Two illustrated children peeking over the video box"></div>
<div class="abs video-box"></div>
<div class="abs video-title">Watch Our Video</div>
<div class="abs rule" style="left:616px;top:304px;width:176px"></div>
<div class="abs video-thumb" role="img" aria-label="Video still of the campaign advert with cardboard characters"></div>
<div class="abs play"><svg width="10" height="12"><path d="M1 0l9 6-9 6z" fill="#222"/></svg></div>
<div class="vbtn" style="left:613px;top:432px;background:var(--green);transform:rotate(-2deg)">Video 1</div>
<div class="vbtn" style="left:704px;top:428px;background:var(--yellow);transform:rotate(-1deg)">Video 2</div>
<div class="vbtn" style="left:626px;top:458px;background:var(--pink);transform:rotate(-1deg)">Video 3</div>
<div class="vbtn" style="left:715px;top:453px;background:var(--blue);transform:rotate(-2deg)">Video 4</div>

<!-- about -->
<h2 class="abs about-title">About Hop Along Days</h2>
<div class="abs rule" style="left:374px;top:547px;width:176px"></div>
<p class="abs about-text">Lorem ipsum dolor sit consectetur adipiscing elituisque fringilla faucibus&nbsp; Pentesqueji habitant morbi tristique senectus et netus malesuada fames ac turpis eras convallisi justo ac cursus molestiesji odio felis aliquet tellus vel blandit mauris msit amet tortork Inrhoncus nisi quis justo mollis non neque sodalese ullamcorpuris ut ultrices gravida est ipsum dictum miac imperdiet nulla nisi vel dLoremk.</p>
<a class="abs more" href="#">READ MORE &#8250;&#8250;</a>

<!-- cards -->
<div class="card c-blue"><span class="arc"></span>
  <div class="icon" style="top:46px;font-size:12px;font-weight:900">Hop Along Days</div>
  <h3>Why Play</h3><p>As an intrinsic part of child hood toys play many different roles.</p><span class="plus">+</span></div>
<div class="card c-pink"><span class="arc"></span>
  <div class="icon"><svg width="34" height="30" viewBox="0 0 34 30"><path d="M4 11h6l16-8v24L10 19H4z" fill="#fff"/><path d="M8 19l3 9h4l-2-9" fill="#fff"/><rect x="27" y="4" width="3" height="22" fill="#fff"/></svg></div>
  <h3>Campaign Purpose</h3><p>Lorem ipsum dolo consectetur adipiscing elituisque faucibus Pentesqueji habitant.</p><span class="plus">+</span></div>
<div class="card c-green"><span class="arc"></span>
  <div class="icon"><svg width="36" height="24" viewBox="0 0 36 24"><path d="M6 3h24c4 0 6 6 6 12s-3 8-6 6l-4-4H10l-4 4c-3 2-6 0-6-6S2 3 6 3z" fill="#fff"/><path d="M9 9v6M6 12h6" stroke="#8cb81a" stroke-width="2"/><circle cx="25" cy="10" r="1.6" fill="#8cb81a"/><circle cx="28" cy="14" r="1.6" fill="#8cb81a"/></svg></div>
  <h3>Fun Forever</h3><p>Lorem ipsum dolo consectetur adipiscing elituisque faucibus Pentesqueji habitant.</p><span class="plus">+</span></div>
<div class="card c-purple"><span class="arc"></span>
  <div class="icon"><svg width="34" height="32" viewBox="0 0 34 32"><path d="M14 12v12l-3-3-3 2 6 8h12l2-10-8-3v-6a3 3 0 0 0-6 0z" fill="none" stroke="#fff" stroke-width="1.6"/><path d="M17 2v4M8 6l3 3M26 6l-3 3M5 13h4" stroke="#fff" stroke-width="1.6"/></svg></div>
  <h3>Play Right Now</h3><p>Lorem ipsum dolo consectetur adipiscing elituisque faucibus Pentesqueji habitant.</p><span class="plus">+</span></div>

<!-- gallery -->
<h2 class="abs gallery-title"><span class="a">Our</span> <span class="b">Gallery</span></h2>
<div class="abs rule" style="left:374px;top:917px;width:176px"></div>
<span class="arrow" style="left:116px">&#171;</span>
<div class="thumb" style="left:146px;transform:rotate(-2deg);background:linear-gradient(135deg,#e94a7a,#f6c53a,#4ab0e6)" role="img" aria-label="Photo of a smiling child in a ball pit"></div>
<div class="thumb" style="left:307px;transform:rotate(-1deg);background:linear-gradient(135deg,#e8e4ef,#8fa6d8,#f2f2f2)" role="img" aria-label="Video still of a girl painting"><span class="play"><svg width="10" height="12"><path d="M1 0l9 6-9 6z" fill="#222"/></svg></span></div>
<div class="thumb" style="left:469px;transform:rotate(-1deg);background:linear-gradient(135deg,#c2302c,#e8a070,#6a2a20)" role="img" aria-label="Video still of children in festive hats crafting"><span class="play"><svg width="10" height="12"><path d="M1 0l9 6-9 6z" fill="#222"/></svg></span></div>
<div class="thumb" style="left:630px;transform:rotate(-2deg);background:linear-gradient(135deg,#d8dad6,#f0d6c4,#b6a896)" role="img" aria-label="Photo of a family baking together"></div>
<span class="arrow" style="left:796px">&#187;</span>

<div class="art" style="left:32px;top:976px;width:112px;height:80px;background:linear-gradient(180deg,#c8865a,#f2b433);border-radius:40px 40px 0 0" role="img" aria-label="Illustrated boy character waving"></div>
<div class="art" style="left:804px;top:976px;width:108px;height:80px;background:linear-gradient(180deg,#d99a5a,#f7dc3a);border-radius:40px 40px 0 0" role="img" aria-label="Illustrated boy character in yellow shirt"></div>

<!-- footer -->
<footer class="abs footer"></footer>
<div class="art" style="left:116px;top:1064px;width:164px;height:126px;background:linear-gradient(135deg,#b87a3e,#d9a35c)" role="img" aria-label="Two cardboard box characters"></div>
<div class="art" style="left:300px;top:1064px;width:132px;height:110px;background:linear-gradient(135deg,#f2d63a,#7fa83a);opacity:.8" role="img" aria-label="Illustrated flower and bees"></div>
<div class="art" style="left:608px;top:1066px;width:44px;height:42px;background:radial-gradient(circle,#f5d21a,#f0e070);border-radius:50%" role="img" aria-label="Illustrated sun"></div>
<div class="art" style="left:472px;top:1118px;width:44px;height:50px;background:linear-gradient(180deg,#f4d232,#6a9a32)" role="img" aria-label="Small illustrated flower"></div>
<div class="abs guild">Northern Games &amp; Crafts Guild</div>
<div class="abs legal">
  &copy; 2014 Northern Games &amp; Crafts Guild Ltd. All Rights Reserved.<br><br style="line-height:4px">
  14 Marlow Lane, Leeds, LS2 7QP<br>
  Click here to read the disclaimer
</div>

</body>
</html>
```